Business card for builder specialising in renovations.

Need a card for our building business. Business name is under Martin Powles.
Have licence number on card ( 527691K)
Contact number (0400 382 415)
Want to work on logo for some business cards and shirts - something with MP or MPB or open to ideas??
No animations, No hammers. Something sharp and eye catching.
Highlight that we are a renovation specialist. Simple on front with extra details on back with some lines to jot down things.

Target Market(s)

Renovators

Industry/Entity Type

Building

Contact Information for Business Card

2 sided with room on back to jot things down.
Extra details on back so front can be simple ..like, renovations, bathrooms, decks, extensions, new builds,

Logo Text

MP

Font styles to use
Serif

Requirements
Must have
• Eye catching design .
• Name : Martin powles
• Licence number
• Contact number - 0400382415
Nice to have
• Some logo design that we can carry through to other forms of advertising
• Local builder
• Quality work
Should not have
• No animations

```html
<!DOCTYPE html>
<html lang="en">
<head>
<meta charset="utf-8">
<title>Martin Powles – Business Card</title>
<link rel="stylesheet" href="https://fonts.googleapis.com/css2?family=Gelasio:wght@400;600&display=swap">
<style>
  :root {
    --bg: #2b2b2b;
    --ink-black: #000000;
    --brand-blue: #1273bb;
    --paper: #ffffff;
    --text-dark: #111111;
    --text-light: #ffffff;
  }
  * { margin: 0; padding: 0; box-sizing: border-box; }
  html, body { width: 1200px; height: 900px; overflow: hidden; background: var(--bg); }
  body { font-family: "Gelasio", Georgia, serif; position: relative; }

  .card {
    position: absolute;
    left: 290px;
    width: 620px;
    height: 354px;
    border-radius: 22px;
    overflow: hidden;
  }

  /* Services side */
  .card--services { top: 60px; background: var(--ink-black); color: var(--text-light); }
  .brand-mark {
    position: absolute; top: 92px; left: 0; right: 0;
    display: flex; justify-content: center; align-items: center; gap: 18px;
  }
  .brand-mark__square { width: 96px; height: 96px; background: var(--brand-blue); }
  .brand-mark__name { font-size: 64px; font-weight: 400; line-height: 1; }
  .card--services .brand-mark__name { color: var(--text-light); }
  .services-list {
    position: absolute; top: 238px; left: 0; right: 0;
    text-align: center; font-size: 16px; letter-spacing: 0.3px;
  }
  .services-web {
    position: absolute; top: 270px; left: 0; right: 0;
    text-align: center; font-size: 17px;
  }
  .accent { color: var(--brand-blue); }

  /* Contact side */
  .card--contact { top: 486px; background: var(--paper); color: var(--text-dark); }
  .side-band {
    position: absolute; top: 0; bottom: 0; left: 0; width: 150px;
    background: var(--brand-blue);
  }
  .contact-mark {
    position: absolute; top: 78px; left: 26px;
    display: flex; align-items: center; gap: 14px;
  }
  .contact-mark__square { width: 100px; height: 100px; background: var(--ink-black); border: 3px solid var(--paper); }
  .contact-mark__name { font-size: 52px; color: var(--ink-black); line-height: 1; }
  .headline {
    position: absolute; top: 44px; left: 178px;
    font-size: 44px; font-weight: 400; color: var(--brand-blue); letter-spacing: 0.5px;
    white-space: nowrap;
  }
  .details { position: absolute; top: 180px; left: 252px; font-size: 15px; line-height: 1.35; }
  .details__name { font-size: 22px; color: var(--brand-blue); letter-spacing: 0.5px; }
  .details__role { margin-bottom: 4px; }
  .details__licence-label { color: var(--brand-blue); }
  .contact-line { display: flex; align-items: center; gap: 9px; }
  .contact-line svg { width: 12px; height: 12px; flex: none; }
</style>
</head>
<body>

  <section class="card card--services" aria-label="Card side with services">
    <div class="brand-mark">
      <span class="brand-mark__square"></span>
      <span class="brand-mark__name">MP</span>
    </div>
    <p class="services-list">RENOVATIONS, BATHROOMS, DECKS, EXTENSIONS, NEW BUILDS,</p>
    <p class="services-web">www.<span class="accent">powlesbuilding</span>.com</p>
  </section>

  <section class="card card--contact" aria-label="Card side with contact details">
    <div class="side-band"></div>
    <div class="contact-mark">
      <span class="contact-mark__square"></span>
      <span class="contact-mark__name">MP</span>
    </div>
    <h1 class="headline">MARTIN POWLES</h1>
    <div class="details">
      <p class="details__name">MARTIN POWLES</p>
      <p class="details__role">Director</p>
      <p><span class="details__licence-label">Licence:</span> (527691K)</p>
      <p class="contact-line">
        <svg viewBox="0 0 12 12" aria-hidden="true"><path d="M2.5 1 L4.5 1 L5 3.5 L3.8 4.4 Q5 7 7.6 8.2 L8.5 7 L11 7.5 L11 9.5 Q10 11 8 10.6 Q2 8.8 1 3 Q1 1.5 2.5 1 Z" fill="var(--brand-blue)"/></svg>
        0400382415
      </p>
      <p class="contact-line">
        <svg viewBox="0 0 12 12" aria-hidden="true"><rect x="1" y="2.5" width="10" height="7" fill="none" stroke="var(--brand-blue)" stroke-width="1.2"/><path d="M1 2.5 L6 6.5 L11 2.5" fill="none" stroke="var(--brand-blue)" stroke-width="1.2"/></svg>
        info@powlesbuilding.com
      </p>
      <p class="contact-line">
        <svg viewBox="0 0 12 12" aria-hidden="true"><circle cx="6" cy="6" r="5" fill="none" stroke="var(--brand-blue)" stroke-width="1.1"/><ellipse cx="6" cy="6" rx="2.2" ry="5" fill="none" stroke="var(--brand-blue)" stroke-width="1"/><path d="M1 6 H11" stroke="var(--brand-blue)" stroke-width="1"/></svg>
        www.<span class="accent">powlesbuilding</span>.com
      </p>
    </div>
  </section>

</body>
</html>
```